Business Card Design - Amberfield Court

We are looking at a new design for our business cards that has a modern and professional look. We run a residential aged care facility focussing on the care of residents. The cards will be used for potential clients, consultants and business opportunities in this sector. Blue and white is our main colours and would to see these colours incorporated in the design.
Industry/Entity Type
Business
Contact Information for Business Card
Amberfield Court, Darren Walsh, dwalsh@amberfieldcourt.com.au, Finance Manager, 0472 639 208, BCom, 37 Marrabel Crescent, Brindle Vale, Qld 4093.
Look and feel
Each slider illustrates characteristics of the customer's brand and the style your logo design should communicate.

```html
<!DOCTYPE html>
<html lang="en">
<head>
<meta charset="utf-8">
<title>Amberfield Court – Business Card</title>
<link rel="stylesheet" href="https://fonts.googleapis.com/css2?family=Open+Sans:wght@400;600;700&display=swap">
<style>
  :root {
    --backdrop: #2b2b2d;
    --navy: #1f3b4b;
    --steel: #4b7d9c;
    --taupe: #b3a79e;
    --paper: #ffffff;
    --ink: #1f3b4b;
    --muted: #3d4f5a;
  }
  * { box-sizing: border-box; margin: 0; padding: 0; }
  html, body { width: 1200px; height: 900px; overflow: hidden; }
  body {
    background: var(--backdrop);
    font-family: "Open Sans", Arial, sans-serif;
    position: relative;
  }
  .card {
    position: absolute;
    width: 560px;
    height: 320px;
    box-shadow: 0 14px 30px rgba(0,0,0,0.45);
  }
  .card-front {
    left: 120px; top: 100px;
    background: var(--navy);
    display: flex; align-items: center; justify-content: center;
  }
  .card-back {
    left: 520px; top: 480px;
    background: var(--paper);
    display: flex; align-items: center;
    padding: 0 24px 0 32px;
    gap: 20px;
  }
  .brand {
    display: flex; align-items: center; gap: 14px;
  }
  .brand-dot {
    width: 46px; height: 46px; border-radius: 50%;
    background: var(--steel);
    flex: none;
  }
  .brand-name {
    font-weight: 600;
    font-size: 28px;
    letter-spacing: 0.04em;
    text-transform: uppercase;
    white-space: nowrap;
  }
  .card-front .brand-name { color: var(--paper); }
  .card-back .brand { width: 250px; flex: none; gap: 12px; }
  .card-back .brand-dot { width: 38px; height: 38px; }
  .card-back .brand-name { color: var(--ink); font-size: 17px; }
  .contact {
    color: var(--muted);
    font-size: 13px;
    line-height: 1.45;
    white-space: nowrap;
  }
  .contact-name {
    font-weight: 700; font-size: 20px; color: var(--ink);
    line-height: 1.1;
  }
  .contact-role {
    font-size: 11px; color: var(--steel); text-transform: uppercase;
    margin-bottom: 6px;
  }
  .contact-line { display: flex; align-items: center; gap: 6px; }
  .contact-line svg { width: 11px; height: 11px; flex: none; }
  .address { margin-bottom: 4px; }
</style>
</head>
<body>
  <section class="card card-front">
    <div class="brand">
      <span class="brand-dot"></span>
      <span class="brand-name">Amberfield Court</span>
    </div>
  </section>

  <section class="card card-back">
    <div class="brand">
      <span class="brand-dot"></span>
      <span class="brand-name">Amberfield Court</span>
    </div>
    <div class="contact">
      <p class="contact-name">DARREN WALSH</p>
      <p class="contact-role">Finance Manager (BCom)</p>
      <p class="address">37 Marrabel Crescent<br>Brindle Vale, Qld 4093</p>
      <p class="contact-line">
        <svg viewBox="0 0 24 24" aria-hidden="true"><path fill="#1f3b4b" d="M6.6 10.8a15 15 0 0 0 6.6 6.6l2.2-2.2a1 1 0 0 1 1-.25 11.4 11.4 0 0 0 3.6.57 1 1 0 0 1 1 1V20a1 1 0 0 1-1 1A17 17 0 0 1 3 4a1 1 0 0 1 1-1h3.5a1 1 0 0 1 1 1c0 1.25.2 2.45.57 3.57a1 1 0 0 1-.25 1z"/></svg>
        0472 639 208
      </p>
      <p class="contact-line">
        <svg viewBox="0 0 24 24" aria-hidden="true"><rect x="2" y="5" width="20" height="14" rx="2" fill="none" stroke="#1f3b4b" stroke-width="2.4"/><path d="M3 6l9 7 9-7" fill="none" stroke="#1f3b4b" stroke-width="2.4"/></svg>
        dwalsh@amberfieldcourt.com.au
      </p>
    </div>
  </section>
</body>
</html>
```